CoinHarbor.com Site Redesign

We are looking to redesign our CoinHarbor.com site. This site is focused on helping consumers make smart financial decisions. We provide reviews and articles in various categories.

We are looking for a responsive design to run on wordpress. We will also have adsense advertisements on our page and will want some ad spot space. We are thinking of two column design vs. single column.

Here is an example of what our competitors look like:
ShopperBeacon.org (mostly reviews vs. articles)
Homepage - https://www.shopperbeacon.example/
Category Review Listing - https://www.shopperbeacon.example/mortgage-refinance/best-mortgage-refinance
Individual Review - https://www.shopperbeacon.example/mortgage-refinance/c/loan-orchard-mortgage-refinance-review

- I like that the site is extremely clean. I like the fixed header in mobile

PilotGuide
Homepage - https://www.pilotguide.example/
Category Review Listing-https://www.pilotguide.example/auto_insurance/index.php
Individual Review- https://www.pilotguide.example/auto_insurance/drivora_review.php

Articles - https://www.pilotguide.example/blog/2017/11/20/going-on-a-holiday-road-trip-be-prepared-for-these-hazards/

What I Like? I like the two column layout in that it gives room for advertising.
What I Do NOT Like? The top navigation is a little cumbersome and old. Mobile view is not very good. Content seems a bit cluttered.

PennyMoth
Homepage - https://www.pennymoth.example
Category Review Listing - https://www.pennymoth.example/blog/insurance/best-car-insurance-companies/?trk=pm_gn1_4.0
Individual Review- https://www.pennymoth.example/blog/insurance/veloro-insurance-review/

What I Like? very clean. Like the use of white space and focus on bright color call to action buttons.
What I Do NOT Like? In mobile a lot of content is pushed below the fold because of the large image above the fold. Reviews are not well organized.

Target Market(s)

consumers interested in saving money and making smart financial decisions

Industry/Entity Type

Financial

Logo Text

CoinHarbor.com or CoinHarbor

Coding

Coded - Design and coding required

Number of Pages Required

5+ page

Font styles to use
Sans Serif

Colors

Designer to choose colors to be used in the design.

Requirements
Must have
• -responsive design
• -room for ad space in the right column
Nice to have
• -good use of white space
• -clean layouts
Should not have
• -clutter

```html
<!DOCTYPE html>
<html lang="en">
<head>
<meta charset="utf-8">
<title>CoinHarbor.com</title>
<link rel="stylesheet" href="https://fonts.googleapis.com/css2?family=Lato:wght@400;700;900&display=swap">
<style>
:root{
  --navy:#0b2d83;
  --blue:#1479c4;
  --ink:#222;
  --muted:#666;
  --line:#d9d9d9;
  --white:#fff;
  --star:#f39a1d;
}
*{box-sizing:border-box;margin:0;padding:0}
html,body{width:1200px;height:3488px;overflow:hidden}
body{font-family:'Lato',sans-serif;color:var(--ink);background:var(--white);position:relative}
.abs{position:absolute}
/* header */
.site-header{position:absolute;left:0;top:0;width:1200px;height:108px;background:var(--white)}
.brand{left:98px;top:34px;display:flex;align-items:center;gap:10px;font-weight:900;font-size:25px;color:var(--navy)}
.brand-mark{width:30px;height:30px;background:var(--blue)}
.top-contact{right:98px;top:28px;font-size:14px;color:var(--muted);display:flex;gap:12px;align-items:center}
.top-contact svg{width:13px;height:13px;fill:var(--blue);vertical-align:-2px;margin-right:6px}
.main-nav{right:98px;top:68px;display:flex;gap:19px;font-size:14px;font-weight:700;color:#333;text-transform:uppercase}
.main-nav .active{color:var(--blue)}
/* hero */
.hero{left:0;top:108px;width:1200px;height:600px}
.hero-photo{position:absolute;inset:0;background:linear-gradient(100deg,#cfc7bd 0%,#a89a8a 35%,#6f6157 60%,#b8b0a6 100%)}
.hero-shape{position:absolute;left:0;top:0;width:1200px;height:600px}
.hero h1{left:0;width:1200px;top:170px;text-align:center;font-size:42px;font-weight:900;color:var(--white);letter-spacing:1px}
.hero .tagline{left:0;width:1200px;top:250px;text-align:center;font-size:20px;color:var(--white)}
.search{left:362px;top:322px;width:472px;height:48px;display:flex}
.search .field{flex:1;background:var(--white);font-size:13px;color:#888;padding:16px 18px}
.search .btn{width:114px;background:var(--navy);color:var(--white);font-weight:700;font-size:15px;text-align:center;line-height:48px;border:2px solid var(--white)}
.arrow{top:225px;color:var(--white);font-size:26px}
.dots{left:574px;top:498px;display:flex;gap:6px}
.dots span{width:11px;height:11px;border-radius:50%;background:var(--white)}
.dots span.on{background:transparent;border:2px solid var(--blue);box-shadow:0 0 0 2px var(--white) inset}
/* shared */
.section-title{left:0;width:1200px;text-align:center;font-size:30px;font-weight:900;color:var(--ink);text-transform:uppercase}
.rule{left:98px;width:1004px;height:1px;background:var(--line)}
/* features */
.subtitle{left:0;width:1200px;top:830px;text-align:center;font-size:14px;font-weight:700;color:var(--navy)}
.feature{top:885px;width:320px;text-align:center}
.feature .icon{width:130px;height:130px;margin:0 auto;border-radius:50%;background:var(--blue);border:5px solid var(--white);box-shadow:0 0 0 2px var(--blue);display:flex;align-items:center;justify-content:center}
.feature .icon svg{width:64px;height:64px;fill:var(--white)}
.feature h3{margin-top:28px;font-size:20px;font-weight:400;color:#333}
.feature p{margin:10px auto 0;width:230px;font-size:14px;line-height:22px;color:var(--muted)}
/* articles */
.article{top:1355px;width:312px}
.article .photo{height:215px}
.article h3{margin-top:30px;font-size:20px;font-weight:700}
.article .meta{margin-top:10px;font-size:13px;color:#555;display:flex;gap:8px;align-items:center}
.article .meta svg{width:12px;height:12px;fill:var(--blue)}
.article p{margin-top:14px;font-size:13px;line-height:22px;color:var(--muted)}
.read-more{display:inline-block;margin-top:20px;border:1px solid #999;padding:7px 16px;font-size:13px;font-weight:700;color:#333}
/* categories */
.col-title{font-size:28px;font-weight:900;text-transform:uppercase}
.tiles{left:98px;top:2020px;width:680px;display:grid;grid-template-columns:repeat(3,218px);grid-auto-rows:164px;gap:12px 13px}
.tile{position:relative;display:flex;align-items:center;justify-content:center;color:var(--white);font-size:17px;font-weight:700;text-shadow:0 1px 3px rgba(0,0,0,.6)}
.show-all{left:330px;top:2576px;width:216px;height:44px;background:var(--navy);color:var(--white);font-weight:700;font-size:16px;text-align:center;line-height:44px}
.ad{left:815px;width:287px}
/* partners */
.partners-sub{left:0;width:1200px;top:2838px;text-align:center;font-size:14px;color:var(--muted)}
.partners{left:98px;top:2895px;width:1004px;display:flex;justify-content:space-between}
.partner{width:188px;height:90px;border:1px solid var(--line);display:flex;flex-direction:column;align-items:center;justify-content:center;gap:10px}
.partner .badge{width:110px;height:28px;background:#e7e9ee;border-radius:4px}
.stars{display:flex;gap:3px}
.stars svg{width:16px;height:16px}
/* footer */
.site-footer{left:0;top:3077px;width:1200px;height:411px;background:var(--navy);color:var(--white)}
.f-col{top:70px}
.f-col h4{font-size:17px;font-weight:900;text-transform:uppercase;margin-bottom:26px}
.f-col li{list-style:none;font-size:13px;line-height:28px}
.f-col li::before{content:"›";margin-right:8px}
.contact-item{display:flex;gap:18px;font-size:13px;line-height:20px;margin-bottom:20px}
.contact-item svg{width:14px;height:14px;fill:var(--white);flex:none;margin-top:3px}
.newsletter p{font-size:13px;line-height:20px;width:250px}
.newsletter .input{margin-top:14px;width:254px;height:34px;border:1px solid var(--white);font-size:12px;padding:10px 12px}
.newsletter .sub{margin-top:14px;display:inline-block;background:var(--white);color:var(--navy);font-size:12px;font-weight:700;padding:8px 14px;border-radius:2px}
.social-line{top:308px;left:98px;width:1004px;height:1px;background:rgba(255,255,255,.6)}
.social{top:290px;left:508px;display:flex;gap:10px;background:var(--navy);padding:0 12px}
.social span{width:36px;height:36px;border-radius:50%;border:2px solid var(--white)}
.copyright{top:362px;left:0;width:1200px;text-align:center;font-size:14px}
</style>
</head>
<body>

<header class="site-header">
  <div class="abs brand"><span class="brand-mark"></span>CoinHarbor.com</div>
  <div class="abs top-contact">
    <span><svg viewBox="0 0 24 24"><path d="M6.6 10.8a15 15 0 0 0 6.6 6.6l2.2-2.2c.3-.3.7-.4 1-.2 1.1.4 2.3.6 3.6.6.6 0 1 .4 1 1V20c0 .6-.4 1-1 1A17 17 0 0 1 3 4c0-.6.4-1 1-1h3.5c.6 0 1 .4 1 1 0 1.3.2 2.5.6 3.6.1.3 0 .7-.2 1z"/></svg>(+1) 555 014 2290</span>
    <span>|</span>
    <span><svg viewBox="0 0 24 24"><path d="M2 5h20v14H2zm2 2v.5l8 5 8-5V7z"/></svg>info@coinharbor.com</span>
  </div>
  <nav class="abs main-nav">
    <span class="active">Home</span><span>Annuities</span><span>Auto Insurance</span><span>Credit Monitoring</span><span>Debt Management</span><span>Mortgages</span>
  </nav>
</header>

<section class="abs hero">
  <div class="hero-photo" role="img" aria-label="Photo of a financial adviser meeting with a smiling couple at a desk"></div>
  <svg class="hero-shape" viewBox="0 0 1200 600" aria-hidden="true">
    <polygon points="0,465 600,580 1200,465 1200,600 0,600" fill="#fff"/>
    <polygon points="0,462 600,572 1200,462 1200,472 600,590 0,472" fill="#0b2d83"/>
    <polygon points="0,458 600,562 1200,458 1200,462 600,568 0,462" fill="#1479c4"/>
  </svg>
  <div class="abs arrow" style="left:40px">‹</div>
  <div class="abs arrow" style="right:40px">›</div>
  <h1 class="abs">COINHARBOR.COM</h1>
  <p class="abs tagline">Make Smarter Financial Decisions Find The Best Financial Products &amp; Service</p>
  <div class="abs search"><div class="field">I'm looking for category</div><div class="btn">SEARCH</div></div>
  <div class="abs dots"><span class="on"></span><span></span><span></span></div>
</section>

<h2 class="abs section-title" style="top:772px">What is CoinHarbor.com?</h2>
<p class="abs subtitle">Financial Service Advice And Reviews</p>

<div class="abs feature" style="left:68px">
  <div class="icon"><svg viewBox="0 0 24 24"><circle cx="10" cy="10" r="6" fill="none" stroke="#fff" stroke-width="2.4"/><path d="M14.5 14.5l6 6" stroke="#fff" stroke-width="3"/></svg></div>
  <h3>We Analyze &amp; Explain</h3>
  <p>We analyze &amp; explain how each online service works</p>
</div>
<div class="abs feature" style="left:440px">
  <div class="icon"><svg viewBox="0 0 24 24"><path d="M5 2h10l5 5v15H5zm9 1.5V8h4.5zM8 11h9v1.5H8zm0 3.5h9V16H8zm0 3.5h9v1.5H8z"/></svg></div>
  <h3>We Test &amp; Compare</h3>
  <p>We test &amp; compare the leading services in each category</p>
</div>
<div class="abs feature" style="left:808px">
  <div class="icon"><svg viewBox="0 0 24 24"><path d="M6 8l1 2.2 2.4.3-1.8 1.6.5 2.4L6 13.3l-2.1 1.2.5-2.4-1.8-1.6 2.4-.3zm12 0l1 2.2 2.4.3-1.8 1.6.5 2.4-2.1-1.2-2.1 1.2.5-2.4-1.8-1.6 2.4-.3zM12 5l1.3 2.8 3 .4-2.2 2 .6 3-2.7-1.5-2.7 1.5.6-3-2.2-2 3-.4z"/></svg></div>
  <h3>We Review &amp; Rate</h3>
  <p>We review and rate each service to show which is best</p>
</div>

<div class="abs rule" style="top:1200px"></div>

<h2 class="abs section-title" style="top:1276px">Recent Articles</h2>

<article class="abs article" style="left:98px">
  <div class="photo" role="img" aria-label="Photo of a couple reviewing paperwork at a table" style="background:linear-gradient(135deg,#7a5a3c,#3f6b3a 60%,#2f2a26)"></div>
  <h3>Discover Undoubtable Source</h3>
  <div class="meta"><svg viewBox="0 0 12 12"><rect x="1" y="2" width="10" height="9"/></svg>02/12/2017 &nbsp;|&nbsp; <svg viewBox="0 0 12 12"><circle cx="6" cy="4" r="2.5"/><path d="M1 12a5 4 0 0 1 10 0z"/></svg>Maren Ostby</div>
  <p>Nam libero tempore, cum soluta nobis est eligendi optio cumque nihil impedit quo minus id quod ma ixime placeat facere possimus</p>
  <span class="read-more">Read More ➜</span>
</article>
<article class="abs article" style="left:444px">
  <div class="photo" role="img" aria-label="Photo of hands using a tablet with financial charts" style="background:linear-gradient(135deg,#f3d9a8,#c7a57a 50%,#6d7aa0)"></div>
  <h3>Discover Undoubtable Source</h3>
  <div class="meta"><svg viewBox="0 0 12 12"><rect x="1" y="2" width="10" height="9"/></svg>02/12/2017 &nbsp;|&nbsp; <svg viewBox="0 0 12 12"><circle cx="6" cy="4" r="2.5"/><path d="M1 12a5 4 0 0 1 10 0z"/></svg>Maren Ostby</div>
  <p>Nam libero tempore, cum soluta nobis est eligendi optio cumque nihil impedit quo minus id quod ma ixime placeat facere possimus</p>
  <span class="read-more">Read More ➜</span>
</article>
<article class="abs article" style="left:790px">
  <div class="photo" role="img" aria-label="Photo of a smiling couple at home" style="background:linear-gradient(135deg,#d8cfc4,#9b8676 55%,#5a6b80)"></div>
  <h3>Discover Undoubtable Source</h3>
  <div class="meta"><svg viewBox="0 0 12 12"><rect x="1" y="2" width="10" height="9"/></svg>02/12/2017 &nbsp;|&nbsp; <svg viewBox="0 0 12 12"><circle cx="6" cy="4" r="2.5"/><path d="M1 12a5 4 0 0 1 10 0z"/></svg>Maren Ostby</div>
  <p>Nam libero tempore, cum soluta nobis est eligendi optio cumque nihil impedit quo minus id quod ma ixime placeat facere possimus</p>
  <span class="read-more">Read More ➜</span>
</article>

<div class="abs rule" style="top:1877px"></div>

<h2 class="abs col-title" style="left:98px;top:1954px">Categories</h2>
<div class="abs tiles">
  <div class="tile" role="img" aria-label="Annuities category photo" style="background:linear-gradient(135deg,#3b9ad8,#1479c4)">Annuities</div>
  <div class="tile" role="img" aria-label="Auto insurance category photo" style="background:linear-gradient(135deg,#6b7480,#3d434c)">Auto Insurance</div>
  <div class="tile" role="img" aria-label="Credit monitoring category photo" style="background:linear-gradient(135deg,#4a5a66,#1f2c36)">Credit Monitoring</div>
  <div class="tile" role="img" aria-label="Credit repair category photo" style="background:linear-gradient(135deg,#8a8a86,#3a3835)">Credit Repair</div>
  <div class="tile" role="img" aria-label="Debt management category photo" style="background:linear-gradient(135deg,#807468,#403832)">Debt Management</div>
  <div class="tile" role="img" aria-label="Identity theft category photo" style="background:linear-gradient(135deg,#7a6a5a,#2f2a28)">Identity Theft</div>
  <div class="tile" role="img" aria-label="Life insurance category photo" style="background:linear-gradient(135deg,#a08a6c,#4f4538)">Life Insurance</div>
  <div class="tile" role="img" aria-label="Mortgages category photo" style="background:linear-gradient(135deg,#bfb2a0,#7a6b58)">Mortgages</div>
  <div class="tile" role="img" aria-label="Online brokerages category photo" style="background:linear-gradient(135deg,#6a7a88,#2c3a46)">Online Brokerages</div>
</div>
<div class="abs show-all">SHOW ALL</div>

<h2 class="abs" style="left:815px;top:1962px;font-size:19px;font-weight:900">RECOMMENDED ARTICLES</h2>
<div class="abs ad" role="img" aria-label="Advertisement for equestrian clothing brands" style="top:2018px;height:237px;background:linear-gradient(180deg,#d81b7a 0 30%,#f4f0f2 30% 100%);border:2px solid #d81b7a"></div>
<div class="abs ad" role="img" aria-label="Advertisement for an equestrian news and directory site" style="top:2288px;height:332px;background:linear-gradient(180deg,#2e8b2e 0 12%,#f6f6f6 12% 58%,#2e8b2e 58% 100%)"></div>

<div class="abs rule" style="top:2705px"></div>

<h2 class="abs section-title" style="top:2782px">Our Partners</h2>
<p class="abs partners-sub">We are focused on helping consumers make smart financial decisions. We provide reviews and articles in various categories.</p>
<div class="abs partners">
  <div class="partner"><span class="badge"></span><div class="stars"><svg viewBox="0 0 24 24"><path fill="#f39a1d" d="M12 2l3 7 7 .6-5.4 4.7 1.7 7.2L12 17.8 5.7 21.5l1.7-7.2L2 9.6 9 9z"/></svg><svg viewBox="0 0 24 24"><path fill="#f39a1d" d="M12 2l3 7 7 .6-5.4 4.7 1.7 7.2L12 17.8 5.7 21.5l1.7-7.2L2 9.6 9 9z"/></svg><svg viewBox="0 0 24 24"><path fill="#f39a1d" d="M12 2l3 7 7 .6-5.4 4.7 1.7 7.2L12 17.8 5.7 21.5l1.7-7.2L2 9.6 9 9z"/></svg><svg viewBox="0 0 24 24"><path fill="#f39a1d" d="M12 2l3 7 7 .6-5.4 4.7 1.7 7.2L12 17.8 5.7 21.5l1.7-7.2L2 9.6 9 9z"/></svg><svg viewBox="0 0 24 24"><path fill="#f39a1d" d="M12 2l3 7 7 .6-5.4 4.7 1.7 7.2L12 17.8 5.7 21.5l1.7-7.2L2 9.6 9 9z"/></svg></div></div>
  <div class="partner"><span class="badge"></span><div class="stars"><svg viewBox="0 0 24 24"><path fill="#f39a1d" d="M12 2l3 7 7 .6-5.4 4.7 1.7 7.2L12 17.8 5.7 21.5l1.7-7.2L2 9.6 9 9z"/></svg><svg viewBox="0 0 24 24"><path fill="#f39a1d" d="M12 2l3 7 7 .6-5.4 4.7 1.7 7.2L12 17.8 5.7 21.5l1.7-7.2L2 9.6 9 9z"/></svg><svg viewBox="0 0 24 24"><path fill="#f39a1d" d="M12 2l3 7 7 .6-5.4 4.7 1.7 7.2L12 17.8 5.7 21.5l1.7-7.2L2 9.6 9 9z"/></svg><svg viewBox="0 0 24 24"><path fill="#f39a1d" d="M12 2l3 7 7 .6-5.4 4.7 1.7 7.2L12 17.8 5.7 21.5l1.7-7.2L2 9.6 9 9z"/></svg><svg viewBox="0 0 24 24"><path fill="#ccc" d="M12 2l3 7 7 .6-5.4 4.7 1.7 7.2L12 17.8 5.7 21.5l1.7-7.2L2 9.6 9 9z"/><path fill="#f39a1d" d="M12 2v15.8L5.7 21.5l1.7-7.2L2 9.6 9 9z"/></svg></div></div>
  <div class="partner"><span class="badge"></span><div class="stars"><svg viewBox="0 0 24 24"><path fill="#f39a1d" d="M12 2l3 7 7 .6-5.4 4.7 1.7 7.2L12 17.8 5.7 21.5l1.7-7.2L2 9.6 9 9z"/></svg><svg viewBox="0 0 24 24"><path fill="#f39a1d" d="M12 2l3 7 7 .6-5.4 4.7 1.7 7.2L12 17.8 5.7 21.5l1.7-7.2L2 9.6 9 9z"/></svg><svg viewBox="0 0 24 24"><path fill="#f39a1d" d="M12 2l3 7 7 .6-5.4 4.7 1.7 7.2L12 17.8 5.7 21.5l1.7-7.2L2 9.6 9 9z"/></svg><svg viewBox="0 0 24 24"><path fill="#f39a1d" d="M12 2l3 7 7 .6-5.4 4.7 1.7 7.2L12 17.8 5.7 21.5l1.7-7.2L2 9.6 9 9z"/></svg><svg viewBox="0 0 24 24"><path fill="#ccc" d="M12 2l3 7 7 .6-5.4 4.7 1.7 7.2L12 17.8 5.7 21.5l1.7-7.2L2 9.6 9 9z"/></svg></div></div>
  <div class="partner"><span class="badge"></span><div class="stars"><svg viewBox="0 0 24 24"><path fill="#f39a1d" d="M12 2l3 7 7 .6-5.4 4.7 1.7 7.2L12 17.8 5.7 21.5l1.7-7.2L2 9.6 9 9z"/></svg><svg viewBox="0 0 24 24"><path fill="#f39a1d" d="M12 2l3 7 7 .6-5.4 4.7 1.7 7.2L12 17.8 5.7 21.5l1.7-7.2L2 9.6 9 9z"/></svg><svg viewBox="0 0 24 24"><path fill="#f39a1d" d="M12 2l3 7 7 .6-5.4 4.7 1.7 7.2L12 17.8 5.7 21.5l1.7-7.2L2 9.6 9 9z"/></svg><svg viewBox="0 0 24 24"><path fill="#ccc" d="M12 2l3 7 7 .6-5.4 4.7 1.7 7.2L12 17.8 5.7 21.5l1.7-7.2L2 9.6 9 9z"/></svg><svg viewBox="0 0 24 24"><path fill="#ccc" d="M12 2l3 7 7 .6-5.4 4.7 1.7 7.2L12 17.8 5.7 21.5l1.7-7.2L2 9.6 9 9z"/></svg></div></div>
  <div class="partner"><span class="badge"></span><div class="stars"><svg viewBox="0 0 24 24"><path fill="#f39a1d" d="M12 2l3 7 7 .6-5.4 4.7 1.7 7.2L12 17.8 5.7 21.5l1.7-7.2L2 9.6 9 9z"/></svg><svg viewBox="0 0 24 24"><path fill="#f39a1d" d="M12 2l3 7 7 .6-5.4 4.7 1.7 7.2L12 17.8 5.7 21.5l1.7-7.2L2 9.6 9 9z"/></svg><svg viewBox="0 0 24 24"><path fill="#ccc" d="M12 2l3 7 7 .6-5.4 4.7 1.7 7.2L12 17.8 5.7 21.5l1.7-7.2L2 9.6 9 9z"/></svg><svg viewBox="0 0 24 24"><path fill="#ccc" d="M12 2l3 7 7 .6-5.4 4.7 1.7 7.2L12 17.8 5.7 21.5l1.7-7.2L2 9.6 9 9z"/></svg><svg viewBox="0 0 24 24"><path fill="#ccc" d="M12 2l3 7 7 .6-5.4 4.7 1.7 7.2L12 17.8 5.7 21.5l1.7-7.2L2 9.6 9 9z"/></svg></div></div>
</div>

<footer class="abs site-footer">
  <div class="abs f-col" style="left:98px">
    <h4>Contact Us</h4>
    <div class="contact-item"><svg viewBox="0 0 24 24"><path d="M12 2a7 7 0 0 0-7 7c0 5 7 13 7 13s7-8 7-13a7 7 0 0 0-7-7zm0 9.5A2.5 2.5 0 1 1 12 6.5a2.5 2.5 0 0 1 0 5z"/></svg><span>Quayside Row, Harbor Town,<br>New State</span></div>
    <div class="contact-item"><svg viewBox="0 0 24 24"><path d="M6.6 10.8a15 15 0 0 0 6.6 6.6l2.2-2.2c.3-.3.7-.4 1-.2 1.1.4 2.3.6 3.6.6.6 0 1 .4 1 1V20c0 .6-.4 1-1 1A17 17 0 0 1 3 4c0-.6.4-1 1-1h3.5c.6 0 1 .4 1 1 0 1.3.2 2.5.6 3.6.1.3 0 .7-.2 1z"/></svg><span>(+1) 555 014 2290</span></div>
    <div class="contact-item"><svg viewBox="0 0 24 24"><path d="M2 5h20v14H2zm2 2v.5l8 5 8-5V7z"/></svg><span>info@coinharbor.com</span></div>
  </div>
  <div class="abs f-col" style="left:395px">
    <h4>Quick Links</h4>
    <ul><li>Annuities</li><li>Auto Insurance</li><li>Credit Monitoring</li><li>Debt Management</li><li>Mortgages</li></ul>
  </div>
  <div class="abs f-col" style="left:630px">
    <h4>Resources</h4>
    <ul><li>Case Studies</li><li>Blog Post</li><li>News</li><li>Privacy Policy</li><li>Terms Of Use</li></ul>
  </div>
  <div class="abs f-col newsletter" style="left:846px">
    <h4>Newsletter Subscription</h4>
    <p>Register your Email Address to get information about us</p>
    <div class="input">Email Address</div>
    <span class="sub">SUBSCRIBE</span>
  </div>
  <div class="abs social-line"></div>
  <div class="abs social" aria-label="Social media links"><span></span><span></span><span></span><span></span></div>
  <p class="abs copyright">Copyrights © 2017 CoinHarbor. All Rights Reserved.</p>
</footer>

</body>
</html>
```